BrimFalcon Business Cards

We have a defined brand. Please visit our website to get a feel for the product and the color pallets. www.brimfalcon-example.com

We need an updated, world class business card design. (See the attached existing card design). Please utilize BOTH sides of the card as shown and be creative with the layout. I do want the horse head icon to be positioned as it is with the existing card.

The remainder of the layout can be customized and I also want it vertically oriented.

Attached are the logo files and please use the colors as follows:
Green - #A5CE39
Tan - #CDBD99
Black

Feel free to play with the colors.

```html
<!DOCTYPE html>
<html lang="en">
<head>
<meta charset="utf-8">
<title>BrimFalcon Labs Business Card</title>
<link href="https://fonts.googleapis.com/css2?family=Open+Sans:wght@400;600&display=swap" rel="stylesheet">
<style>
  :root {
    --backdrop: #e4e4e2;
    --card: #2e2f31;
    --card-deep: #232426;
    --green: #a5ce39;
    --green-name: #7fb22e;
    --white: #ffffff;
    --muted: #e8e8e8;
  }
  * { margin: 0; padding: 0; box-sizing: border-box; }
  html, body { width: 1200px; height: 801px; overflow: hidden; }
  body {
    background: var(--backdrop);
    font-family: "Open Sans", Arial, sans-serif;
    position: relative;
  }
  .card {
    position: absolute;
    top: 112px;
    width: 330px;
    height: 577px;
    background: var(--card);
    border-bottom: 3px solid var(--green);
    border-left: 3px solid var(--green);
    box-shadow: 0 10px 24px rgba(0,0,0,0.18);
    overflow: hidden;
  }
  .card--front { left: 235px; }
  .card--back { left: 635px; }

  .brand { display: flex; align-items: center; gap: 10px; }
  .brand__mark { border-radius: 50%; background: var(--white); flex: none; }
  .brand__name { color: var(--white); font-weight: 600; letter-spacing: 0.5px; }

  .emblem {
    position: absolute;
    right: -50px; top: -40px;
    width: 300px; height: 300px;
    border-radius: 50%;
    background: radial-gradient(circle at 60% 40%, #3a3b3e, var(--card-deep) 70%);
    box-shadow: inset 0 0 18px rgba(0,0,0,0.35);
  }

  .front__brand { position: absolute; left: 28px; top: 290px; }
  .front__brand .brand__mark { width: 30px; height: 30px; }
  .front__brand .brand__name { font-size: 24px; white-space: nowrap; }
  .tagline {
    position: absolute;
    left: 68px; top: 326px;
    color: var(--white);
    font-size: 11px;
    letter-spacing: 2.4px;
    white-space: nowrap;
  }

  .contact { position: absolute; left: 68px; top: 372px; color: var(--muted); }
  .contact__name {
    color: var(--green-name);
    font-size: 19px;
    font-weight: 600;
    letter-spacing: 0.5px;
  }
  .contact__title { font-size: 13px; margin-bottom: 12px; }
  .contact__address { font-size: 13px; line-height: 1.35; margin-bottom: 12px; }
  .contact__list { list-style: none; font-size: 13px; line-height: 1.5; }
  .contact__list li { display: flex; align-items: center; gap: 7px; white-space: nowrap; }
  .contact__list svg { width: 10px; height: 10px; flex: none; }

  .back__brand {
    position: absolute;
    left: 0; right: 0; top: 0; bottom: 0;
    flex-direction: column;
    justify-content: center;
    gap: 16px;
  }
  .back__brand .brand__mark { width: 56px; height: 56px; }
  .back__brand .brand__name { font-size: 34px; white-space: nowrap; }
</style>
</head>
<body>

  <section class="card card--front">
    <div class="emblem" role="img" aria-label="Large embossed brand emblem in dark tones"></div>

    <div class="brand front__brand">
      <span class="brand__mark"></span>
      <span class="brand__name">BrimFalcon Labs</span>
    </div>
    <p class="tagline">Performance Driven EVs</p>

    <div class="contact">
      <p class="contact__name">DANA MERROW</p>
      <p class="contact__title">President &amp; CEO</p>
      <p class="contact__address">Maple Ridge, Westland<br>Canada</p>
      <ul class="contact__list">
        <li>
          <svg viewBox="0 0 10 10"><path d="M2 1 L4 1 L4.6 3 L3.5 4 Q4.5 6 6 6.5 L7 5.4 L9 6 L9 8 Q9 9 8 9 Q1 8.5 1 2 Q1 1 2 1Z" fill="#a5ce39"/></svg>
          555.010.4821
        </li>
        <li>
          <svg viewBox="0 0 10 10"><rect x="0.5" y="2" width="9" height="6.5" fill="#a5ce39"/><path d="M0.5 2 L5 5.5 L9.5 2" stroke="#2e2f31" stroke-width="1" fill="none"/></svg>
          Dana@BrimFalcon-example.com
        </li>
        <li>
          <svg viewBox="0 0 10 10"><circle cx="5" cy="5" r="4.3" fill="none" stroke="#a5ce39" stroke-width="1.2"/><path d="M1 5 H9 M5 1 Q2.5 5 5 9 M5 1 Q7.5 5 5 9" stroke="#a5ce39" stroke-width="0.9" fill="none"/></svg>
          BrimFalconLabs-example.com
        </li>
      </ul>
    </div>
  </section>

  <section class="card card--back">
    <div class="brand back__brand">
      <span class="brand__mark"></span>
      <span class="brand__name">BrimFalcon Labs</span>
    </div>
  </section>

</body>
</html>
```